Business Card Design

New business card design

Target Market(s)

Residential & Commercial Property Managers

Industry/Entity Type

Plumbing Services

Contact Information for Business Card

Name - Rowan Keddle, title - Director, Phone Number - 0431 286 517, email - rowan@tbk-plumbing.com.au, Company ABN - 73 215 904 386,

Font styles to use
Sans Serif

Colors
0054AA
0677BA
7BADD7
CADEEF
E8F1F8

```html
<!DOCTYPE html>
<html lang="en">
<head>
<meta charset="utf-8">
<title>TBK Plumbing Services – Business Card</title>
<link rel="stylesheet" href="https://fonts.googleapis.com/css2?family=Poppins:wght@300;400;500;600&display=swap">
<style>
  :root {
    --stage: #222222;
    --card-light: #ebe9e7;
    --brand-blue: #29a3da;
    --band-blue: #2a9fd4;
    --navy: #14202c;
    --warm-grey: #6f6660;
    --ink: #111111;
    --white: #ffffff;
    --emboss: #1b86bd;
  }
  * { box-sizing: border-box; margin: 0; padding: 0; }
  html, body { width: 1200px; height: 780px; overflow: hidden; }
  body {
    background: var(--stage);
    font-family: "Poppins", sans-serif;
    display: flex;
    align-items: center;
    justify-content: center;
    gap: 40px;
  }
  .card {
    position: relative;
    width: 540px;
    height: 310px;
    border-radius: 22px;
    overflow: hidden;
  }

  /* Front */
  .card-front { background: var(--card-light); }
  .front-band { position: absolute; inset: 0; width: 100%; height: 100%; }
  .front-logo {
    position: absolute; left: 150px; top: 28px;
    display: flex; align-items: center; gap: 12px;
    color: var(--navy); font-weight: 300;
  }
  .front-logo .logo-dot {
    width: 16px; height: 16px; border-radius: 50%; background: var(--brand-blue);
  }
  .front-logo .logo-name { font-size: 52px; line-height: 1; letter-spacing: 2px; }
  .front-logo .logo-tag { font-size: 11px; letter-spacing: 6px; margin-top: 4px; }
  .abn {
    position: absolute; left: 130px; top: 126px;
    font-size: 12px; font-weight: 300; color: var(--brand-blue);
  }
  .contact-list {
    position: absolute; left: 26px; top: 196px;
    list-style: none; color: var(--white);
    font-size: 13px; font-weight: 300; line-height: 1.55;
  }
  .contact-list li { display: flex; align-items: center; gap: 8px; }
  .contact-list svg { width: 12px; height: 12px; flex: none; }
  .person {
    position: absolute; right: 34px; top: 146px; text-align: right;
  }
  .person-name { font-size: 28px; line-height: 1.1; color: var(--warm-grey); font-weight: 300; }
  .person-name .first { color: var(--brand-blue); font-weight: 600; }
  .person-title { font-size: 14px; color: var(--ink); margin-top: 2px; }
  .side-tab {
    position: absolute; right: 0; top: 190px; width: 14px; height: 44px;
    background: var(--brand-blue);
  }

  /* Back */
  .card-back {
    background: var(--brand-blue);
    display: flex; align-items: center; justify-content: center;
  }
  .back-logo {
    display: flex; align-items: center; gap: 16px;
    color: var(--emboss); font-weight: 300;
  }
  .back-logo .logo-dot {
    width: 20px; height: 20px; border-radius: 50%; background: var(--white);
  }
  .back-logo .logo-name { font-size: 72px; line-height: 1; letter-spacing: 3px; }
  .back-logo .logo-tag { font-size: 13px; letter-spacing: 7px; margin-top: 6px; }
</style>
</head>
<body>
  <section class="card card-front" aria-label="Business card front">
    <svg class="front-band" viewBox="0 0 540 310" preserveAspectRatio="none" aria-hidden="true">
      <polygon points="0,150 450,310 0,310" fill="var(--band-blue)"/>
    </svg>

    <div class="front-logo">
      <span class="logo-dot"></span>
      <div>
        <div class="logo-name">tbk</div>
        <div class="logo-tag">plumbing services</div>
      </div>
    </div>

    <p class="abn">ABN - 73 215 904 386</p>

    <ul class="contact-list">
      <li>
        <svg viewBox="0 0 24 24" aria-hidden="true"><path fill="currentColor" d="M6.6 10.8a15 15 0 0 0 6.6 6.6l2.2-2.2c.3-.3.7-.4 1-.2 1.1.4 2.3.6 3.6.6.6 0 1 .4 1 1V20c0 .6-.4 1-1 1A17 17 0 0 1 3 4c0-.6.4-1 1-1h3.5c.6 0 1 .4 1 1 0 1.3.2 2.5.6 3.6.1.3 0 .7-.2 1z"/></svg>
        0431 286 517
      </li>
      <li>
        <svg viewBox="0 0 24 24" aria-hidden="true"><circle cx="12" cy="12" r="9" fill="none" stroke="currentColor" stroke-width="2"/><path d="M3 12h18M12 3c3 3 3 15 0 18M12 3c-3 3-3 15 0 18" fill="none" stroke="currentColor" stroke-width="1.6"/></svg>
        www.tbk-plumbing.com.au
      </li>
      <li>
        <svg viewBox="0 0 24 24" aria-hidden="true"><rect x="3" y="5" width="18" height="14" rx="2" fill="none" stroke="currentColor" stroke-width="2"/><path d="M3 6l9 7 9-7" fill="none" stroke="currentColor" stroke-width="2"/></svg>
        rowan@tbk-plumbing.com.au
      </li>
    </ul>

    <div class="person">
      <p class="person-name"><span class="first">Rowan</span> Keddle</p>
      <p class="person-title">Director</p>
    </div>
    <span class="side-tab"></span>
  </section>

  <section class="card card-back" aria-label="Business card back">
    <div class="back-logo">
      <span class="logo-dot"></span>
      <div>
        <div class="logo-name">tbk</div>
        <div class="logo-tag">plumbing services</div>
      </div>
    </div>
  </section>
</body>
</html>
```